Launching a new real estate agency in Monaco

Hello, I am opening a new real estate agency in Monaco. For the purpose of my activity, in order to be known quickly among a fierce competition I need an advertising campaign that will be broadcast in local magazines, newspapers, paper board, etc.

You will find example of pictures of Monaco on which I have the rights and my logo. You can always pick other images that I can buy if the price is reasonable for a commercial use (<200 $)

Please respect the color code.

I wish you good luck and look forward to give you my feedbacks

Reason: Only few projects posted were respecting the brief and of quality. Hoping to receive more in coming days

Target Market(s)

International high-end clientele of all ages, all genders.

Industry/Entity Type

Real Estate Agent

Font styles to use
Serif

Requirements
Must have
• 1/ My logo
• 2/ This message "Un nouveau regard sur l'immobilier" means in English a fresh look at real estate or new eyes on real-estate.
• 3/ My address: 14 rue des Ormeaux, Galerie Bellerive Nord, 98 000 Monaco
• 4/ Phone number: +377.93.48.25.07
• 5/ Website: www.corvano-immo.com.
• 6/ Format: Files should be easily adjustable but I'd like a vertical display to fit easily in Magazines, Poster and billboard. So please work in high resolution !
Nice to have
• Please think about your design in accordance with the message I want to display.
Should not have
• A simple poster with a picture of Monaco that does not take into consideration the message of the advertisement, "Un nouveau regard sur l'immobilier" which means in english, new eyes on real-estate or a new look at real-estate, or new vision at real-estate.

```html
<!DOCTYPE html>
<html lang="fr">
<head>
<meta charset="utf-8">
<title>Corvano Immo — Un Nouveau Regard Sur L'immobilier</title>
<link href="https://fonts.googleapis.com/css2?family=Playfair+Display:wght@700;800&family=Arimo:wght@400;700&display=swap" rel="stylesheet">
<style>
  :root {
    --backdrop: #d8d5d1;
    --navy: #2b3d59;
    --black: #000000;
    --salmon: #e8a790;
    --salmon-soft: #e9b3a0;
    --sky: #5aa3e0;
    --sea: #1f5fa8;
    --cliff: #4d6a3a;
    --roof: #d9774f;
  }
  * { margin: 0; padding: 0; box-sizing: border-box; }
  html, body {
    width: 1200px; height: 1200px; overflow: hidden;
    background: var(--backdrop);
  }
  .poster {
    position: absolute;
    left: 220px; top: 32px;
    width: 760px; height: 1136px;
    background: var(--navy);
    overflow: hidden;
  }
  .poster__frame {
    position: absolute; inset: 0;
    width: 100%; height: 100%;
  }
  .poster__website {
    position: absolute;
    left: 60px; top: 46px;
    font-family: "Arimo", Arial, sans-serif;
    font-size: 17px;
    color: var(--salmon);
    letter-spacing: 0.2px;
  }
  .poster__headline {
    position: absolute;
    left: 0; right: 0; top: 618px;
    text-align: center;
    font-family: "Playfair Display", "Bodoni Moda", serif;
    font-weight: 800;
    font-size: 86px;
    line-height: 110px;
    color: var(--salmon);
  }
  .poster__footer {
    position: absolute;
    left: 0; right: 0; top: 1012px;
    height: 94px;
  }
  .brand {
    position: absolute;
    left: 60px; top: 30px;
    display: flex; align-items: center; gap: 12px;
  }
  .brand__mark {
    width: 26px; height: 26px;
    background: var(--salmon);
  }
  .brand__name {
    font-family: "Playfair Display", serif;
    font-weight: 700;
    font-size: 26px;
    color: var(--salmon);
    letter-spacing: 1px;
  }
  .footer__divider {
    position: absolute;
    left: 378px; top: 0;
    width: 2px; height: 94px;
    background: var(--salmon);
  }
  .contact {
    position: absolute;
    left: 404px; top: 20px;
    font-family: "Arimo", Arial, sans-serif;
    color: var(--salmon-soft);
  }
  .contact__phone {
    font-weight: 700;
    font-size: 23px;
    color: var(--salmon);
    margin-bottom: 6px;
  }
  .contact__address {
    font-size: 15px;
    line-height: 20px;
  }
</style>
</head>
<body>
  <main class="poster">
    <svg class="poster__frame" viewBox="0 0 692 1036" preserveAspectRatio="none" aria-hidden="false">
      <defs>
        <linearGradient id="view-fill" x1="0" y1="0" x2="0" y2="1">
          <stop offset="0" stop-color="var(--sky)"/>
          <stop offset="0.25" stop-color="#8cc3ee"/>
          <stop offset="0.3" stop-color="var(--sea)"/>
          <stop offset="0.55" stop-color="var(--cliff)"/>
          <stop offset="0.8" stop-color="var(--roof)"/>
          <stop offset="1" stop-color="#b85a3c"/>
        </linearGradient>
      </defs>
      <g class="binocular-mask" fill="var(--black)">
        <rect x="0" y="0" width="692" height="432"/>
        <ellipse cx="175" cy="312" rx="208" ry="220"/>
        <ellipse cx="517" cy="312" rx="208" ry="220"/>
      </g>
      <g class="binocular-view" role="img" aria-label="Vue panoramique de Monaco : le Rocher, le port et la mer, vus à travers des jumelles" fill="url(#view-fill)">
        <ellipse cx="186" cy="315" rx="162" ry="158"/>
        <ellipse cx="506" cy="315" rx="162" ry="158"/>
      </g>
    </svg>

    <p class="poster__website">www.corvano-immo.com</p>

    <h1 class="poster__headline">Un Nouveau<br>Regard Sur<br>L'immobilier</h1>

    <footer class="poster__footer">
      <div class="brand">
        <span class="brand__mark"></span>
        <span class="brand__name">CORVANO IMMO</span>
      </div>
      <span class="footer__divider"></span>
      <div class="contact">
        <p class="contact__phone">+377.93.48.25.07</p>
        <p class="contact__address">14 rue des Ormeaux, Galerie Bellerive Nord<br>98 000 Monaco</p>
      </div>
    </footer>
  </main>
</body>
</html>
```